Redesign business cards

We have a new logo and I am not that happy with the layout of our existing card and looking for a change. Font is a bit small and the green can be hard to read. Logo may need a tidy up as the copy I have is not that hi-res too so require you to produce a hi-res version of the logo for us too. There will be three individual business cards to produce with just the names and phone numbers being different. Address will change too, but use what you see on the card for now.

Industry/Entity Type

Business

Requirements
Nice to have
• You could consider a redesign to the new logo, just not too radical. We like the blue and green hexagons as we feel that they are representative of oil industry that we are in.

```html
<!DOCTYPE html>
<html lang="en">
<head>
<meta charset="utf-8">
<title>Verdax Oil Services — Business Card Set</title>
<link rel="stylesheet" href="https://fonts.googleapis.com/css2?family=Exo:wght@400;500;600;700&display=swap">
<style>
  :root {
    --backdrop: #e9e6e1;
    --card: #ffffff;
    --card-shade: #f0f0f0;
    --ink: #3f4043;
    --ink-soft: #4c4d50;
    --green: #7cc242;
    --green-deep: #4e9a28;
    --orange: #f7941d;
    --grey-band: #6d6e71;
    --white: #ffffff;
  }
  * { box-sizing: border-box; margin: 0; padding: 0; }
  html, body {
    width: 1057px; height: 1200px; overflow: hidden;
    background: var(--backdrop);
    font-family: "Exo", "Trebuchet MS", sans-serif;
  }
  .sheet {
    width: 1057px; height: 1200px;
    display: grid;
    grid-template-columns: repeat(2, 309px);
    grid-template-rows: repeat(2, 540px);
    gap: 50px 70px;
    justify-content: center; align-content: center;
  }
  .card {
    position: relative;
    width: 309px; height: 540px;
    background: radial-gradient(ellipse at 60% 30%, var(--card) 45%, var(--card-shade) 100%);
    box-shadow: 0 12px 30px rgba(0,0,0,.16);
    overflow: hidden;
  }

  .brand { position: absolute; display: flex; align-items: center; gap: 10px; color: var(--ink); }
  .brand__mark { width: 26px; height: 26px; background: var(--green); flex: none; }
  .brand__name { font-weight: 600; font-size: 36px; line-height: 1; }
  .brand__tag { font-weight: 600; font-size: 14px; line-height: 1.2; margin-top: 3px; }
  .card--front .brand { top: 38px; right: 28px; }
  .card--back .brand { top: 180px; left: 50%; transform: translateX(-50%); }
  .card--back .brand__mark { width: 32px; height: 32px; }
  .card--back .brand__name { font-size: 44px; }
  .card--back .brand__tag { font-size: 17px; }

  .contact { position: absolute; top: 140px; left: 28px; right: 20px; list-style: none; }
  .contact__item {
    display: flex; align-items: center; gap: 10px;
    font-size: 14px; line-height: 1.3; font-weight: 500; color: var(--ink-soft);
    margin-bottom: 9px;
  }
  .contact__item--address { align-items: flex-start; }
  .contact__icon {
    width: 22px; height: 22px; border-radius: 4px; background: var(--green-deep); flex: none;
    display: flex; align-items: center; justify-content: center;
  }
  .contact__icon svg { width: 14px; height: 14px; }

  .band { position: absolute; left: 0; bottom: 0; width: 309px; height: 160px; }
  .band svg { display: block; width: 100%; height: 100%; }
  .band__text {
    position: absolute; left: 0; right: 0; bottom: 22px;
    padding: 0 26px; text-align: right; color: var(--white);
  }
  .holder__name { font-size: 22px; font-weight: 700; letter-spacing: 1.5px; text-transform: uppercase; line-height: 1.15; }
  .holder__role { font-size: 13px; font-weight: 600; letter-spacing: 2px; text-transform: uppercase; margin-top: 4px; }
  .website { font-size: 17px; font-weight: 600; letter-spacing: .5px; }
</style>
</head>
<body>
<main class="sheet">

  <!-- Front: Daniel Reeve -->
  <section class="card card--front" aria-label="Card front, Daniel Reeve">
    <div class="brand">
      <span class="brand__mark"></span>
      <div><div class="brand__name">Verdax</div><div class="brand__tag">Oil Services</div></div>
    </div>
    <ul class="contact">
      <li class="contact__item contact__item--address">
        <span class="contact__icon"><svg viewBox="0 0 16 16"><path d="M8 1a5 5 0 0 0-5 5c0 4 5 9 5 9s5-5 5-9a5 5 0 0 0-5-5zm0 7a2 2 0 1 1 0-4 2 2 0 0 1 0 4z" fill="#fff"/></svg></span>
        <span>42 Harbour Line Road,<br>2nd Floor, Quay West</span>
      </li>
      <li class="contact__item"><span class="contact__icon"><svg viewBox="0 0 16 16"><path d="M4 1l3 3-2 2c1 2 3 4 5 5l2-2 3 3-2 2C7 14 2 9 2 3z" fill="#fff"/></svg></span><span>014 552 3190</span></li>
      <li class="contact__item"><span class="contact__icon"><svg viewBox="0 0 16 16"><rect x="4" y="1" width="8" height="14" rx="1.5" fill="#fff"/><rect x="6" y="3" width="4" height="7" fill="#4e9a28"/></svg></span><span>078 214 6603</span></li>
      <li class="contact__item"><span class="contact__icon"><svg viewBox="0 0 16 16"><rect x="2" y="5" width="12" height="8" fill="#fff"/><rect x="4" y="2" width="8" height="4" fill="#fff"/><rect x="5" y="8" width="6" height="1.5" fill="#4e9a28"/></svg></span><span>014 552 3199</span></li>
      <li class="contact__item"><span class="contact__icon"><svg viewBox="0 0 16 16"><rect x="1.5" y="3.5" width="13" height="9" fill="#fff"/><path d="M1.5 3.5 8 9l6.5-5.5" fill="none" stroke="#4e9a28" stroke-width="1.4"/></svg></span><span>info@verdaxoil.com</span></li>
      <li class="contact__item"><span class="contact__icon"><svg viewBox="0 0 16 16"><circle cx="8" cy="8" r="6" fill="none" stroke="#fff" stroke-width="1.5"/><path d="M2 8h12M8 2c-3 3-3 9 0 12M8 2c3 3 3 9 0 12" fill="none" stroke="#fff" stroke-width="1.2"/></svg></span><span>www.verdaxoil.com</span></li>
    </ul>
    <div class="band">
      <svg viewBox="0 0 309 160" preserveAspectRatio="none" aria-hidden="true">
        <path d="M0 30 C100 10 220 14 309 42 L309 160 L0 160 Z" fill="var(--grey-band)"/>
        <path d="M0 48 C100 28 220 32 309 62 L309 160 L0 160 Z" fill="var(--orange)"/>
        <path d="M0 62 C110 40 220 48 309 76 L309 160 L0 160 Z" fill="var(--green-deep)"/>
      </svg>
      <div class="band__text"><div class="holder__name">Daniel Reeve</div><div class="holder__role">General Manager</div></div>
    </div>
  </section>

  <!-- Front: Priya Nandal -->
  <section class="card card--front" aria-label="Card front, Priya Nandal">
    <div class="brand">
      <span class="brand__mark"></span>
      <div><div class="brand__name">Verdax</div><div class="brand__tag">Oil Services</div></div>
    </div>
    <ul class="contact">
      <li class="contact__item contact__item--address">
        <span class="contact__icon"><svg viewBox="0 0 16 16"><path d="M8 1a5 5 0 0 0-5 5c0 4 5 9 5 9s5-5 5-9a5 5 0 0 0-5-5zm0 7a2 2 0 1 1 0-4 2 2 0 0 1 0 4z" fill="#fff"/></svg></span>
        <span>42 Harbour Line Road,<br>2nd Floor, Quay West</span>
      </li>
      <li class="contact__item"><span class="contact__icon"><svg viewBox="0 0 16 16"><path d="M4 1l3 3-2 2c1 2 3 4 5 5l2-2 3 3-2 2C7 14 2 9 2 3z" fill="#fff"/></svg></span><span>014 552 3194</span></li>
      <li class="contact__item"><span class="contact__icon"><svg viewBox="0 0 16 16"><rect x="4" y="1" width="8" height="14" rx="1.5" fill="#fff"/><rect x="6" y="3" width="4" height="7" fill="#4e9a28"/></svg></span><span>078 330 9147</span></li>
      <li class="contact__item"><span class="contact__icon"><svg viewBox="0 0 16 16"><rect x="2" y="5" width="12" height="8" fill="#fff"/><rect x="4" y="2" width="8" height="4" fill="#fff"/><rect x="5" y="8" width="6" height="1.5" fill="#4e9a28"/></svg></span><span>014 552 3199</span></li>
      <li class="contact__item"><span class="contact__icon"><svg viewBox="0 0 16 16"><rect x="1.5" y="3.5" width="13" height="9" fill="#fff"/><path d="M1.5 3.5 8 9l6.5-5.5" fill="none" stroke="#4e9a28" stroke-width="1.4"/></svg></span><span>info@verdaxoil.com</span></li>
      <li class="contact__item"><span class="contact__icon"><svg viewBox="0 0 16 16"><circle cx="8" cy="8" r="6" fill="none" stroke="#fff" stroke-width="1.5"/><path d="M2 8h12M8 2c-3 3-3 9 0 12M8 2c3 3 3 9 0 12" fill="none" stroke="#fff" stroke-width="1.2"/></svg></span><span>www.verdaxoil.com</span></li>
    </ul>
    <div class="band">
      <svg viewBox="0 0 309 160" preserveAspectRatio="none" aria-hidden="true">
        <path d="M0 30 C100 10 220 14 309 42 L309 160 L0 160 Z" fill="var(--grey-band)"/>
        <path d="M0 48 C100 28 220 32 309 62 L309 160 L0 160 Z" fill="var(--orange)"/>
        <path d="M0 62 C110 40 220 48 309 76 L309 160 L0 160 Z" fill="var(--green-deep)"/>
      </svg>
      <div class="band__text"><div class="holder__name">Priya Nandal</div><div class="holder__role">Operations Manager</div></div>
    </div>
  </section>

  <!-- Front: Tom Hollis -->
  <section class="card card--front" aria-label="Card front, Tom Hollis">
    <div class="brand">
      <span class="brand__mark"></span>
      <div><div class="brand__name">Verdax</div><div class="brand__tag">Oil Services</div></div>
    </div>
    <ul class="contact">
      <li class="contact__item contact__item--address">
        <span class="contact__icon"><svg viewBox="0 0 16 16"><path d="M8 1a5 5 0 0 0-5 5c0 4 5 9 5 9s5-5 5-9a5 5 0 0 0-5-5zm0 7a2 2 0 1 1 0-4 2 2 0 0 1 0 4z" fill="#fff"/></svg></span>
        <span>42 Harbour Line Road,<br>2nd Floor, Quay West</span>
      </li>
      <li class="contact__item"><span class="contact__icon"><svg viewBox="0 0 16 16"><path d="M4 1l3 3-2 2c1 2 3 4 5 5l2-2 3 3-2 2C7 14 2 9 2 3z" fill="#fff"/></svg></span><span>014 552 3197</span></li>
      <li class="contact__item"><span class="contact__icon"><svg viewBox="0 0 16 16"><rect x="4" y="1" width="8" height="14" rx="1.5" fill="#fff"/><rect x="6" y="3" width="4" height="7" fill="#4e9a28"/></svg></span><span>078 641 2285</span></li>
      <li class="contact__item"><span class="contact__icon"><svg viewBox="0 0 16 16"><rect x="2" y="5" width="12" height="8" fill="#fff"/><rect x="4" y="2" width="8" height="4" fill="#fff"/><rect x="5" y="8" width="6" height="1.5" fill="#4e9a28"/></svg></span><span>014 552 3199</span></li>
      <li class="contact__item"><span class="contact__icon"><svg viewBox="0 0 16 16"><rect x="1.5" y="3.5" width="13" height="9" fill="#fff"/><path d="M1.5 3.5 8 9l6.5-5.5" fill="none" stroke="#4e9a28" stroke-width="1.4"/></svg></span><span>info@verdaxoil.com</span></li>
      <li class="contact__item"><span class="contact__icon"><svg viewBox="0 0 16 16"><circle cx="8" cy="8" r="6" fill="none" stroke="#fff" stroke-width="1.5"/><path d="M2 8h12M8 2c-3 3-3 9 0 12M8 2c3 3 3 9 0 12" fill="none" stroke="#fff" stroke-width="1.2"/></svg></span><span>www.verdaxoil.com</span></li>
    </ul>
    <div class="band">
      <svg viewBox="0 0 309 160" preserveAspectRatio="none" aria-hidden="true">
        <path d="M0 30 C100 10 220 14 309 42 L309 160 L0 160 Z" fill="var(--grey-band)"/>
        <path d="M0 48 C100 28 220 32 309 62 L309 160 L0 160 Z" fill="var(--orange)"/>
        <path d="M0 62 C110 40 220 48 309 76 L309 160 L0 160 Z" fill="var(--green-deep)"/>
      </svg>
      <div class="band__text"><div class="holder__name">Tom Hollis</div><div class="holder__role">Sales Manager</div></div>
    </div>
  </section>

  <!-- Shared back -->
  <section class="card card--back" aria-label="Card back">
    <div class="brand">
      <span class="brand__mark"></span>
      <div><div class="brand__name">Verdax</div><div class="brand__tag">Oil Services</div></div>
    </div>
    <div class="band">
      <svg viewBox="0 0 309 160" preserveAspectRatio="none" aria-hidden="true">
        <path d="M0 30 C100 10 220 14 309 42 L309 160 L0 160 Z" fill="var(--grey-band)"/>
        <path d="M0 48 C100 28 220 32 309 62 L309 160 L0 160 Z" fill="var(--orange)"/>
        <path d="M0 62 C110 40 220 48 309 76 L309 160 L0 160 Z" fill="var(--green-deep)"/>
      </svg>
      <div class="band__text"><div class="website">www.verdaxoil.com</div></div>
    </div>
  </section>

</main>
</body>
</html>
```